Weightloss company needs Business Card

We want a business card that is clean and professional, yet portrays that we are a friendly, innovative, and versatile program designed to fit the needs of our clients.
I would like there to be 2 sides, one side having an appointment card, and the other side containing the logo and business information. There can be decorations on both sides. The logo is attached.

Target Market(s)

Men and women 40-60

Industry/Entity Type

Business

Contact Information for Business Card

Font styles to use
Sans Serif

Requirements
Must have
• The logo, space for business information
Nice to have
• The colors in the logo
Should not have
• No pictures of people or food

```html
<!DOCTYPE html>
<html lang="en">
<head>
<meta charset="utf-8">
<title>Renew Turn Wellness – Business Card</title>
<link rel="stylesheet" href="https://fonts.googleapis.com/css2?family=Open+Sans:wght@400;600;700&display=swap">
<style>
  :root {
    --brand-red: #ee1b3a;
    --brand-red-dark: #e0142f;
    --ink-white: #ffffff;
    --paper: #fbfbfb;
    --backdrop: #e9e6e3;
    --dots: #222222;
  }
  * { box-sizing: border-box; margin: 0; padding: 0; }
  html, body {
    width: 1200px; height: 900px; overflow: hidden;
    background: var(--backdrop);
    font-family: "Open Sans", Arial, sans-serif;
  }
  .stage { position: relative; width: 1200px; height: 900px; }

  .card {
    position: absolute;
    width: 556px; height: 343px;
    overflow: hidden;
    box-shadow: 0 6px 18px rgba(0,0,0,.18);
  }

  /* Front: contact side */
  .card--front {
    left: 238px; top: 62px;
    background: var(--brand-red);
    color: var(--ink-white);
  }
  .holder { position: absolute; left: 33px; top: 64px; }
  .holder__name { font-size: 21px; font-weight: 600; line-height: 1.2; }
  .holder__role { font-size: 15px; font-weight: 400; }
  .address {
    position: absolute; left: 33px; top: 166px;
    font-size: 14.5px; line-height: 20px;
  }
  .contacts {
    position: absolute; left: 33px; top: 215px;
    list-style: none; font-size: 14.5px; line-height: 20px;
  }
  .contacts li { display: flex; align-items: center; gap: 9px; }
  .contacts svg { width: 12px; height: 12px; fill: var(--ink-white); flex: none; }

  .brand {
    position: absolute; display: flex; align-items: center; gap: 12px;
    font-weight: 700; font-size: 28px; line-height: 30px;
  }
  .brand__name { white-space: nowrap; text-align: left; }
  .brand__dot { width: 14px; height: 14px; border-radius: 50%; flex: none; }
  .card--front .brand { left: 276px; top: 144px; color: var(--ink-white); }
  .card--front .brand__dot { background: var(--ink-white); }

  /* Back: appointment side */
  .card--back {
    left: 458px; top: 518px;
    width: 560px;
    background: var(--paper);
    color: var(--brand-red-dark);
    text-align: center;
  }
  .card--back .brand {
    left: 0; right: 0; top: 64px; justify-content: center;
    color: var(--brand-red-dark);
  }
  .card--back .brand__dot { background: var(--brand-red-dark); }
  .appointment__title {
    position: absolute; left: 0; right: 0; top: 162px;
    font-size: 21px; font-weight: 600;
  }
  .appointment__fields {
    position: absolute; left: 99px; top: 209px; width: 360px;
    font-size: 14px; font-weight: 700; text-align: left;
  }
  .field-row { display: flex; align-items: flex-end; height: 22px; margin-bottom: 20px; }
  .field-label { white-space: nowrap; margin-right: 3px; }
  .field-line { flex: 1; border-bottom: 2px dotted var(--dots); height: 14px; }
  .field-line--date { flex: 0 0 166px; }
  .appointment__note {
    position: absolute; left: 0; right: 0; top: 292px;
    font-size: 14px; font-weight: 600;
  }
</style>
</head>
<body>
<main class="stage">

  <section class="card card--front" aria-label="Card front with contact details">
    <div class="holder">
      <p class="holder__name">Daniel Harper</p>
      <p class="holder__role">Managing Director</p>
    </div>
    <p class="address">12345, Address Goes Here<br>Country Name, 123456.</p>
    <ul class="contacts">
      <li>
        <svg viewBox="0 0 24 24" aria-hidden="true"><path d="M6.6 10.8a15 15 0 0 0 6.6 6.6l2.2-2.2a1 1 0 0 1 1-.25 11.4 11.4 0 0 0 3.6.57 1 1 0 0 1 1 1V20a1 1 0 0 1-1 1A17 17 0 0 1 3 4a1 1 0 0 1 1-1h3.5a1 1 0 0 1 1 1c0 1.25.2 2.450.57 3.57a1 1 0 0 1-.25 1z"/></svg>
        044-555 010 234
      </li>
      <li>
        <svg viewBox="0 0 24 24" aria-hidden="true"><path d="M2 5h20v14H2z M2 5l10 8 10-8" fill="none" stroke="#fff" stroke-width="2.4"/></svg>
        hello@renewturn.com
      </li>
      <li>
        <svg viewBox="0 0 24 24" aria-hidden="true"><circle cx="12" cy="12" r="10"/></svg>
        www.renewturn.com
      </li>
    </ul>
    <div class="brand"><span class="brand__dot"></span><span class="brand__name">Renew Turn<br>Wellness</span></div>
  </section>

  <section class="card card--back" aria-label="Card back with appointment form">
    <div class="brand"><span class="brand__dot"></span><span class="brand__name">Renew Turn<br>Wellness</span></div>
    <h2 class="appointment__title">Your Next Appointment is</h2>
    <div class="appointment__fields">
      <div class="field-row">
        <span class="field-label">Name:</span><span class="field-line"></span>
      </div>
      <div class="field-row">
        <span class="field-label">Date:</span><span class="field-line field-line--date"></span>
        <span class="field-label">Time:</span><span class="field-line"></span>
      </div>
    </div>
    <p class="appointment__note">If unable to keep appointment,&nbsp; kindly give 24hrs notice.</p>
  </section>

</main>
</body>
</html>
```